Veltrano.co - Polar Expeditions Specialists

We need a modern, visually striking business card for Veltrano.co, a company specialized in selling expedition cruises to the most remote regions on Earth, with a focus on the Arctic and Antarctica. The design should instantly communicate that the cardholder is an expert in polar travel. Use clean, premium aesthetics with cool tones like icy blue and white, possibly incorporating polar imagery (ice, glaciers, penguins, etc.)

Attached the logo

Contact Information for Business Card

Feels high-end and trustworthy.. Visually memorable — encourages people to keep it

Colors
0054AA
0677BA
7BADD7
CADEEF
E8F1F8

Requirements
Must have
• ice, glaciers, penguins, montains
Nice to have
• modern, transparente,

```html
<!DOCTYPE html>
<html lang="en">
<head>
<meta charset="UTF-8">
<title>Veltrano.co – Business Card</title>
<link rel="stylesheet" href="https://fonts.googleapis.com/css2?family=Poppins:wght@400;500;600;700&display=swap">
<style>
  :root {
    --navy: #12142b;
    --navy-soft: #1e2548;
    --brand-blue: #3a78bf;
    --white: #ffffff;
    --ice: #e8f1f8;
    --page: #dfe4ea;
  }
  * { box-sizing: border-box; margin: 0; padding: 0; }
  html, body {
    width: 1200px; height: 900px; overflow: hidden;
    background: var(--page);
    font-family: "Poppins", sans-serif;
  }
  .sheet {
    position: relative; width: 1200px; height: 900px;
    display: flex; flex-direction: column; align-items: center; justify-content: center; gap: 44px;
  }
  .card {
    position: relative; width: 620px; height: 354px;
    border-radius: 26px; overflow: hidden;
    box-shadow: 0 10px 30px rgba(18, 20, 43, 0.25);
  }
  /* Front */
  .card--front { background: var(--navy); }
  .front-scenery {
    position: absolute; right: -30px; top: 30px; width: 300px; height: 360px;
    border-radius: 45% 45% 0 0;
    background: radial-gradient(ellipse at 50% 35%, rgba(58, 120, 191, 0.22), rgba(30, 37, 72, 0.55) 55%, rgba(18, 20, 43, 0) 80%);
  }
  .front-brand {
    position: absolute; inset: 0;
    display: flex; flex-direction: column; align-items: center; justify-content: center;
    padding-top: 40px;
    color: var(--white);
  }
  .brand-row { display: flex; align-items: center; gap: 12px; }
  .brand-dot { width: 16px; height: 16px; border-radius: 50%; background: var(--white); flex: none; }
  .brand-name { font-weight: 700; font-size: 56px; letter-spacing: 1px; line-height: 1; white-space: nowrap; }
  .brand-tagline { font-weight: 500; font-size: 18px; margin-top: 10px; white-space: nowrap; }
  /* Back */
  .card--back { background: var(--navy); }
  .back-shape { position: absolute; inset: 0; }
  .contact {
    position: absolute; left: 40px; top: 62px; color: var(--white);
  }
  .contact::before {
    content: ""; position: absolute; left: -40px; top: 4px;
    width: 5px; height: 36px; background: var(--brand-blue);
  }
  .contact-name { font-weight: 700; font-size: 27px; color: var(--brand-blue); line-height: 1.1; }
  .contact-role { font-size: 15px; margin-bottom: 18px; }
  .contact-address { font-size: 14.5px; line-height: 1.45; margin-bottom: 14px; }
  .contact-list { list-style: none; font-size: 14.5px; line-height: 1.55; }
  .contact-list li { display: flex; align-items: center; gap: 9px; }
  .contact-list svg { width: 13px; height: 13px; fill: var(--white); flex: none; }
  .back-scenery {
    position: absolute; left: 380px; top: 300px; width: 200px; height: 36px;
    border-radius: 50% 50% 0 0;
    background: linear-gradient(180deg, var(--ice), rgba(232, 241, 248, 0));
  }
  .back-brand {
    position: absolute; left: 340px; right: 14px; top: 0; bottom: 0;
    display: flex; flex-direction: column; align-items: center; justify-content: center;
    padding-top: 30px;
    color: var(--brand-blue);
  }
  .back-brand .brand-name { font-size: 38px; letter-spacing: 0.5px; }
  .back-brand .brand-dot { width: 12px; height: 12px; background: var(--brand-blue); }
  .back-brand .brand-row { gap: 9px; }
  .back-brand .brand-tagline { font-size: 12.5px; margin-top: 6px; }
</style>
</head>
<body>
<main class="sheet">
  <section class="card card--front" aria-label="Card front">
    <div class="front-scenery" role="img" aria-label="Faint polar wildlife and ice scenery in deep blue"></div>
    <div class="front-brand">
      <div class="brand-row">
        <span class="brand-dot"></span>
        <span class="brand-name">Veltrano.co</span>
      </div>
      <p class="brand-tagline">Polar Expeditions Specialists</p>
    </div>
  </section>

  <section class="card card--back" aria-label="Card back">
    <svg class="back-shape" viewBox="0 0 620 354" preserveAspectRatio="none" aria-hidden="true">
      <path d="M378 354 C 300 290 300 120 410 42 C 440 20 470 8 500 0 L 620 0 L 620 354 Z" fill="var(--white)"/>
      <path d="M366 354 C 320 310 306 250 318 180 C 314 250 332 310 384 354 Z" fill="var(--brand-blue)"/>
    </svg>
    <div class="back-scenery" role="img" aria-label="Soft icy glacier horizon"></div>

    <div class="contact">
      <h1 class="contact-name">Marlon Reyes</h1>
      <p class="contact-role">CEO &amp; Founder</p>
      <p class="contact-address">47 Harbor Point Lane,<br>Westbrook, ME 04092 USA</p>
      <ul class="contact-list">
        <li><svg viewBox="0 0 16 16"><path d="M3 1h3l1.5 4-2 1.2a9 9 0 0 0 4.3 4.3L11 8.5l4 1.5v3c0 1-1 2-2 2A13 13 0 0 1 1 3c0-1 1-2 2-2z"/></svg>+1.207.555.014</li>
        <li><svg viewBox="0 0 16 16"><path d="M1 3h14v10H1z M1 3l7 6 7-6" stroke="#12142b" stroke-width="1.2"/></svg>hello@veltranomail.com</li>
        <li><svg viewBox="0 0 16 16"><circle cx="8" cy="8" r="7"/><path d="M1 8h14M8 1c3 3 3 11 0 14M8 1c-3 3-3 11 0 14" stroke="#12142b" stroke-width="1.1" fill="none"/></svg>www.veltranotravel.com</li>
      </ul>
    </div>

    <div class="back-brand">
      <div class="brand-row">
        <span class="brand-dot"></span>
        <span class="brand-name">Veltrano.co</span>
      </div>
      <p class="brand-tagline">Polar Expeditions Specialists</p>
    </div>
  </section>
</main>
</body>
</html>
```